Business card for medical clinic

I need an upmarket, modern medical/health business card for my clinic

Contact Information for Business Card

name, address, email, qr code

```html
<!DOCTYPE html>
<html lang="en">
<head>
<meta charset="utf-8">
<title>Solenne Health Partners – Business Card</title>
<link rel="stylesheet" href="https://fonts.googleapis.com/css2?family=Montserrat:wght@400;500;700&display=swap">
<style>
  :root {
    --backdrop: #d2d2d2;
    --card: #f1f1ef;
    --navy: #123d66;
    --sky: #2aa3dc;
    --ink-grey: #6d6d6d;
    --edge: #35a8e0;
  }
  * { margin: 0; padding: 0; box-sizing: border-box; }
  html, body {
    width: 1200px;
    height: 1051px;
    overflow: hidden;
    background: var(--backdrop);
    font-family: "Montserrat", sans-serif;
  }
  .sheet {
    width: 1200px;
    height: 1051px;
    display: flex;
    align-items: center;
    justify-content: center;
    gap: 56px;
  }
  .card {
    width: 490px;
    height: 280px;
    background: var(--card);
    border-bottom: 4px solid var(--edge);
    box-shadow: 0 18px 40px rgba(0,0,0,0.18);
    position: relative;
    display: flex;
    flex-direction: column;
    align-items: center;
    justify-content: center;
  }
  /* Contact side */
  .contact { text-align: center; }
  .contact__name {
    color: var(--navy);
    font-weight: 700;
    font-size: 19px;
    letter-spacing: 0.5px;
    text-transform: uppercase;
  }
  .contact__role {
    color: var(--ink-grey);
    font-size: 13px;
    margin-top: 4px;
  }
  .contact__rule {
    width: 48px;
    height: 2px;
    background: var(--sky);
    margin: 14px auto 12px;
  }
  .contact__line {
    color: var(--ink-grey);
    font-size: 12.5px;
    line-height: 1.55;
  }
  .contact__accent { color: var(--sky); }
  /* Brand side */
  .brand {
    display: flex;
    align-items: center;
    gap: 14px;
  }
  .brand__dot {
    width: 34px;
    height: 34px;
    border-radius: 50%;
    background: var(--sky);
  }
  .brand__name {
    color: var(--navy);
    font-weight: 500;
    font-size: 24px;
    letter-spacing: 1px;
    text-transform: uppercase;
  }
</style>
</head>
<body>
  <main class="sheet">
    <section class="card card--contact">
      <div class="contact">
        <h1 class="contact__name">Adrian Kelwick</h1>
        <p class="contact__role">President</p>
        <div class="contact__rule"></div>
        <p class="contact__line">949-555-0187</p>
        <p class="contact__line">adrian@SolenneHealth.com</p>
        <p class="contact__line">www.<span class="contact__accent">SolenneHealth</span>.com</p>
        <p class="contact__line">18 Harbor View Lane, Coastview CA 90000</p>
      </div>
    </section>
    <section class="card card--brand">
      <div class="brand">
        <span class="brand__dot"></span>
        <span class="brand__name">Solenne Health Partners</span>
      </div>
    </section>
  </main>
</body>
</html>
```